New Bicycle shop business card

Hi!
I'm looking for a business card for my new proffesional bike mechanics shop. This shop is only for fixing broken bikes and not selling bikes.
Peferbly a modern and sleek and modern design.
Colors: black, grey, red, white
Information:
Name: Rijwielwerkplaats Vanhoutte
Shop owner: Bart Vanhoutte & Marieke Segers
Website: www.rijwielwerkplaats-vanhoutte.be
Email: info@rijwielwerkplaats-vanhoutte.be
Phone number: +32471902368
Street adres: Kerkweg 46
9940 Bellebeke
Slogan/shop information: Herstellingen van alle merken.
Logo: see files.
Target Market(s)
People who seek a mechanic to fix or upgrade their bikes.
Contact Information for Business Card
Information:
Website: info@rijwielwerkplaats-vanhoutte.be
9940 Bellebeke
Logo: see files.

```html
<!DOCTYPE html>
<html lang="nl">
<head>
<meta charset="utf-8">
<title>Rijwielwerkplaats Vanhoutte – visitekaartje</title>
<link href="https://fonts.googleapis.com/css2?family=Josefin+Sans:wght@600;700&family=Roboto:wght@400;500&display=swap" rel="stylesheet">
<style>
  :root {
    --page-bg: #e4e1de;
    --card-light: #f5f4f2;
    --brand-red: #c8283a;
    --brand-red-dark: #a81e2e;
    --ink: #1d1b1c;
    --cream: #f3dccd;
    --cream-soft: #ecc7b8;
  }
  * { box-sizing: border-box; margin: 0; padding: 0; }
  html, body {
    width: 1200px; height: 1054px; overflow: hidden;
    background: var(--page-bg);
  }
  .card {
    position: absolute; left: 100px; top: 227px;
    width: 1000px; height: 600px;
    background: var(--card-light);
    box-shadow: 0 18px 40px rgba(0,0,0,0.18);
    overflow: hidden;
  }
  .card-shape { position: absolute; inset: 0; }
  .brand {
    position: absolute; left: 40px; top: 130px; width: 420px;
    text-align: center;
  }
  .brand-mark {
    width: 78px; height: 78px; border-radius: 50%;
    background: var(--brand-red); margin: 0 auto 34px;
  }
  .brand-name {
    font-family: "Josefin Sans", sans-serif; font-weight: 700;
    font-size: 31px; line-height: 1.2; letter-spacing: 2px;
    color: var(--ink); text-transform: uppercase;
  }
  .brand-tagline {
    margin-top: 26px;
    font-family: "Roboto", sans-serif; font-size: 21px; color: var(--ink);
  }
  .contact {
    position: absolute; left: 576px; top: 140px;
    font-family: "Roboto", sans-serif; color: var(--cream);
  }
  .contact-name {
    font-family: "Josefin Sans", sans-serif; font-weight: 700;
    font-size: 33px; letter-spacing: 1.5px; text-transform: uppercase;
  }
  .contact-role { font-size: 24px; color: var(--cream-soft); margin-top: 6px; }
  .contact-list { list-style: none; margin-top: 40px; }
  .contact-list li {
    display: flex; align-items: center; height: 38px; font-size: 20px;
  }
  .contact-list svg { width: 22px; height: 22px; margin-right: 18px; fill: var(--cream-soft); flex: none; }
  .contact-address { margin-top: 26px; font-size: 22px; line-height: 38px; color: var(--cream-soft); padding-left: 50px; }
</style>
</head>
<body>
<div class="card">
  <svg class="card-shape" viewBox="0 0 1000 600" width="1000" height="600" aria-hidden="true">
    <path d="M410 0 Q600 300 410 600 L1000 600 L1000 0 Z" fill="var(--ink)"/>
    <path d="M430 0 Q612 300 436 600 L1000 600 L1000 0 Z" fill="var(--brand-red)"/>
    <path d="M700 0 L1000 0 L1000 600 L620 600 Q880 300 700 0 Z" fill="var(--brand-red-dark)" opacity="0.25"/>
  </svg>

  <div class="brand">
    <div class="brand-mark"></div>
    <div class="brand-name">Rijwielwerkplaats<br>Vanhoutte</div>
    <div class="brand-tagline">Herstellingen van alle merken</div>
  </div>

  <div class="contact">
    <div class="contact-name">Marieke Segers</div>
    <div class="contact-role">Owner</div>
    <ul class="contact-list">
      <li><svg viewBox="0 0 24 24"><path d="M3 8c0-2 3-4 9-4s9 2 9 4v2h-5V8H8v2H3z M6 12h12l2 8H4z M9 15h6v2H9z"/></svg>+32471902368</li>
      <li><svg viewBox="0 0 24 24"><path d="M2 5h20v14H2z M4 7v.5l8 6 8-6V7z" fill-rule="evenodd"/></svg>www.rijwielwerkplaats-vanhoutte.be</li>
      <li><svg viewBox="0 0 24 24"><circle cx="12" cy="12" r="9" fill="none" stroke="var(--cream-soft)" stroke-width="2"/><path d="M3 12h18M12 3c-4 5-4 13 0 18M12 3c4 5 4 13 0 18" fill="none" stroke="var(--cream-soft)" stroke-width="1.6"/></svg>info@rijwielwerkplaats-vanhoutte.be</li>
    </ul>
    <div class="contact-address">Kerkweg 46<br>9940 Bellebeke</div>
  </div>
</div>
</body>
</html>
```